Design a product reviews website

We need a website design and simple logo for the brand Venlotix.com. The website will provide reviews of technology products and services. The brand and website should be approachable but should also be trustworthy and high quality. The deliverable should be designs, specs and assets that I can provide to a development team to build the website.

Target Market(s)

People researching products to buy.

Industry/Entity Type

Product

Logo Text

Venlotix.com

Number of Pages Required

5+ page

Font styles to use
Sans Serif

Colors
0492cd
0355a3
3176b5
33a6d7
85cae6
85abd2
cedeed
cee9f5

Requirements
Must have
• - Designs for the Homepage, Category and Article pages.
• - Designs for web and mobile.
• - Designs details for the engineering team to use for development.
• - I'm open to other colors than the preferences I chose but I'm more likely to like blues, greys and blacks.

```html
<!DOCTYPE html>
<html lang="en">
<head>
<meta charset="utf-8">
<title>Venlotix.com – Product and Services Reviews</title>
<link rel="stylesheet" href="https://fonts.googleapis.com/css2?family=Lato:wght@400;700&display=swap">
<style>
  :root{
    --brand:#0492cd;
    --brand-dark:#0355a3;
    --nav:#1a6fc0;
    --bar:#3176b5;
    --ink:#222;
    --muted:#8a8a8a;
    --page:#ececec;
    --card:#fff;
    --footer:#2b2b2b;
    --tag:#3b82c8;
  }
  *{box-sizing:border-box;margin:0;padding:0}
  html,body{width:702px;height:1200px;overflow:hidden}
  body{font-family:'Lato',sans-serif;background:var(--page);color:var(--ink);position:relative}

  .site-header{position:absolute;top:0;left:0;width:702px;height:58px;background:#fff;display:flex;align-items:center;padding:0 47px}
  .brand-name{font-size:25px;font-weight:400;color:var(--brand-dark);letter-spacing:.2px}
  .search{margin-left:auto;display:flex;align-items:center}
  .search-field{width:180px;height:22px;border:1px solid #c9c9c9;font-size:10px;color:#999;padding:4px 6px;background:#fff}
  .search-button{width:24px;height:22px;background:var(--brand);display:flex;align-items:center;justify-content:center;margin-left:4px}
  .menu-button{width:28px;height:28px;border-radius:50%;background:var(--brand);display:flex;align-items:center;justify-content:center;margin-left:12px}

  .hero{position:absolute;top:58px;left:0;width:702px;height:254px;background:linear-gradient(100deg,#d8d4cc 0%,#a7a49e 22%,#e9e5dd 45%,#cfc9bf 70%,#8d8a86 100%)}
  .hero-caption{position:absolute;left:0;bottom:0;width:100%;height:38px;background:rgba(20,20,20,.72);color:#fff;font-size:20px;display:flex;align-items:center;justify-content:center;letter-spacing:.2px}
  .hero-arrow{position:absolute;top:126px;width:16px;height:24px;background:rgba(0,0,0,.55);display:flex;align-items:center;justify-content:center}
  .hero-arrow.prev{left:0}
  .hero-arrow.next{right:0}

  .main-nav{position:absolute;top:312px;left:0;width:702px;height:33px;background:var(--nav);display:flex;align-items:center;padding-left:58px;gap:0}
  .main-nav a{color:#fff;text-decoration:none;font-size:11px;padding:0 12px;height:33px;display:flex;align-items:center;position:relative}
  .main-nav a.active{font-weight:700}
  .main-nav a.active::after{content:"";position:absolute;left:50%;bottom:0;transform:translateX(-50%);border:5px solid transparent;border-bottom-color:#fff}

  .section-bar{height:33px;background:var(--bar);color:#fff;font-size:19px;display:flex;align-items:center;padding:0 8px;margin-bottom:2px}
  .section-bar .pager{margin-left:auto;display:flex;gap:3px}

  .latest{position:absolute;top:377px;left:47px;width:428px}
  .card-grid{display:grid;grid-template-columns:210px 210px;column-gap:8px;row-gap:9px}
  .card{background:var(--card)}
  .card.wide{grid-column:1 / span 2}
  .card-media{position:relative;height:161px}
  .card.wide .card-media{height:169px}
  .tags{position:absolute;left:6px;bottom:6px;display:flex;gap:3px}
  .tag{background:var(--tag);color:#fff;font-size:9px;padding:3px 6px}
  .card-title{font-size:14px;font-weight:700;padding:9px 8px 0}
  .card-meta{display:flex;align-items:center;padding:8px 8px 10px;font-size:9px}
  .avatar{width:16px;height:16px;background:#9a8f86;margin-right:6px}
  .author{color:var(--brand-dark);font-weight:700;font-size:10px}
  .posted{margin-left:auto;color:var(--muted);font-size:8px}
  .row-gap{height:5px}

  .popular{position:absolute;top:377px;left:487px;width:168px}
  .popular-item{background:var(--card);margin-bottom:6px}
  .popular-media{position:relative;height:135px}
  .popular-title{font-size:12px;font-weight:700;padding:9px 6px 9px}

  .load-more{position:absolute;top:1138px;left:315px;width:72px;height:20px;background:var(--brand-dark);color:#fff;font-size:9px;font-weight:700;display:flex;align-items:center;justify-content:center}

  .site-footer{position:absolute;left:0;bottom:0;width:702px;height:30px;background:var(--footer);color:#ddd;font-size:9px;display:flex;align-items:center;justify-content:center}
</style>
</head>
<body>

<header class="site-header">
  <div class="brand-name">Venlotix.com</div>
  <div class="search">
    <div class="search-field">Search</div>
    <div class="search-button">
      <svg width="12" height="12" viewBox="0 0 12 12"><circle cx="5" cy="5" r="3.5" fill="none" stroke="#fff" stroke-width="1.6"/><line x1="7.6" y1="7.6" x2="11" y2="11" stroke="#fff" stroke-width="1.8"/></svg>
    </div>
  </div>
  <div class="menu-button">
    <svg width="14" height="12" viewBox="0 0 14 12"><rect y="1" width="14" height="2" fill="#fff"/><rect y="5" width="14" height="2" fill="#fff"/><rect y="9" width="14" height="2" fill="#fff"/></svg>
  </div>
</header>

<section class="hero" role="img" aria-label="Living room with a television, speakers and home electronics by a window">
  <div class="hero-arrow prev"><svg width="8" height="12" viewBox="0 0 8 12"><path d="M6 1 1 6l5 5" fill="none" stroke="#fff" stroke-width="2"/></svg></div>
  <div class="hero-arrow next"><svg width="8" height="12" viewBox="0 0 8 12"><path d="M2 1l5 5-5 5" fill="none" stroke="#fff" stroke-width="2"/></svg></div>
  <div class="hero-caption">The Best Product and Services Reviews and Rankings</div>
</section>

<nav class="main-nav">
  <a class="active">Home</a><a>Appliances</a><a>Computers</a><a>Electronics</a><a>Home Security</a><a>Mobile</a><a>Smart Home</a><a>Software</a>
</nav>

<section class="latest">
  <div class="section-bar">New
    <div class="pager">
      <svg width="10" height="14" viewBox="0 0 10 14"><path d="M8 1 2 7l6 6" fill="none" stroke="#cfe4f5" stroke-width="2"/></svg>
      <svg width="10" height="14" viewBox="0 0 10 14"><path d="M2 1l6 6-6 6" fill="none" stroke="#cfe4f5" stroke-width="2"/></svg>
    </div>
  </div>
  <div class="card-grid">
    <article class="card">
      <div class="card-media" role="img" aria-label="Wall-mounted television showing a sunset landscape" style="background:linear-gradient(180deg,#e7dcd2 0%,#c98a5a 45%,#3a2a22 100%)">
        <div class="tags"><span class="tag">Home</span><span class="tag">Television</span></div>
      </div>
      <h3 class="card-title">Lorem Ipsum Dolor Sit Amet</h3>
      <div class="card-meta"><span class="avatar" role="img" aria-label="Author photo"></span><span class="author">John Smith</span><span class="posted">Posted On 21 Aug, 2016</span></div>
    </article>
    <article class="card">
      <div class="card-media" role="img" aria-label="Laptop with a colourful tile screen" style="background:linear-gradient(160deg,#f4f4f4 0%,#c9ccd0 45%,#5a8fc4 75%,#e6e6e6 100%)">
        <div class="tags"><span class="tag">Home</span><span class="tag">Laptop</span></div>
      </div>
      <h3 class="card-title">Lorem Ipsum Dolor Sit Amet</h3>
      <div class="card-meta"><span class="avatar" role="img" aria-label="Author photo"></span><span class="author">John Smith</span><span class="posted">Posted On 21 Aug, 2016</span></div>
    </article>
    <article class="card wide">
      <div class="card-media" role="img" aria-label="Lounge with a yellow sofa, pendant lamps and wall speakers" style="background:linear-gradient(180deg,#3d3d3f 0%,#6a6a6a 45%,#c9b84a 70%,#8b7b64 100%)">
        <div class="tags"><span class="tag">Home</span><span class="tag">Speakers</span></div>
      </div>
      <h3 class="card-title">Lorem Ipsum Dolor Sit Amet</h3>
      <div class="card-meta"><span class="avatar" role="img" aria-label="Author photo"></span><span class="author">John Smith</span><span class="posted">Posted On 21 Aug, 2016</span></div>
    </article>
    <article class="card">
      <div class="card-media" role="img" aria-label="Home theatre speaker set" style="background:linear-gradient(180deg,#f2f2f2 0%,#d9d9d9 40%,#5b3a2c 70%,#2a1d18 100%)">
        <div class="tags"><span class="tag">Home</span><span class="tag">Speakers</span></div>
      </div>
      <h3 class="card-title">Lorem Ipsum Dolor Sit Amet</h3>
      <div class="card-meta"><span class="avatar" role="img" aria-label="Author photo"></span><span class="author">John Smith</span><span class="posted">Posted On 21 Aug, 2016</span></div>
    </article>
    <article class="card">
      <div class="card-media" role="img" aria-label="Security camera mounted on a wall" style="background:linear-gradient(150deg,#b8bcc0 0%,#e3e4e5 45%,#7b7f84 100%)">
        <div class="tags"><span class="tag">Home</span><span class="tag">Security Camera</span></div>
      </div>
      <h3 class="card-title">Lorem Ipsum Dolor Sit Amet</h3>
      <div class="card-meta"><span class="avatar" role="img" aria-label="Author photo"></span><span class="author">John Smith</span><span class="posted">Posted On 21 Aug, 2016</span></div>
    </article>
  </div>
</section>

<aside class="popular">
  <div class="section-bar">Popular
    <div class="pager">
      <svg width="10" height="14" viewBox="0 0 10 14"><path d="M8 1 2 7l6 6" fill="none" stroke="#cfe4f5" stroke-width="2"/></svg>
      <svg width="10" height="14" viewBox="0 0 10 14"><path d="M2 1l6 6-6 6" fill="none" stroke="#cfe4f5" stroke-width="2"/></svg>
    </div>
  </div>
  <article class="popular-item">
    <div class="popular-media" role="img" aria-label="Row of copper pots" style="background:linear-gradient(180deg,#6b3a1e 0%,#c9823f 50%,#e0a860 100%)">
      <div class="tags"><span class="tag">Copper Pots</span></div>
    </div>
    <h3 class="popular-title">Lorem Ipsum Dolor Sit Amet</h3>
  </article>
  <article class="popular-item">
    <div class="popular-media" role="img" aria-label="Smartphone with a blue screen" style="background:linear-gradient(180deg,#f5f5f5 0%,#7fb2e0 40%,#3a6fb0 65%,#f0f0f0 100%)">
      <div class="tags"><span class="tag">Mobile</span></div>
    </div>
    <h3 class="popular-title">Lorem Ipsum Dolor Sit Amet</h3>
  </article>
  <article class="popular-item">
    <div class="popular-media" role="img" aria-label="Stainless steel refrigerator in a kitchen" style="background:linear-gradient(90deg,#e8e6e2 0%,#b9bbbd 35%,#d8dadb 60%,#9b9690 100%)">
      <div class="tags"><span class="tag">Refrigerator</span></div>
    </div>
    <h3 class="popular-title">Lorem Ipsum Dolor Sit Amet</h3>
  </article>
  <article class="popular-item">
    <div class="popular-media" role="img" aria-label="Washing machine and dryer side by side" style="background:linear-gradient(180deg,#eaeaea 0%,#cfd3d6 50%,#9aa0a5 100%)">
      <div class="tags"><span class="tag">Washing Machine</span></div>
    </div>
    <h3 class="popular-title">Lorem Ipsum Dolor Sit Amet</h3>
  </article>
</aside>

<div class="load-more">Load More &rarr;</div>

<footer class="site-footer">Copyright 2016 Venlotix.com. All Rights Reserved.</footer>

</body>
</html>
```